Lune Rouge Studio (Masterclasses for Actors) needs artistic and modern website in French & English

Hello!

We need to create a new website (existing : www.lune-rouge-studio.example) for our acting school that holds Masterclasses for professional actors in Paris. It needs to be in French and English with an easy to use back office (wordpress is slow and complicated) (ideas?) so we can add or change workshop dates, upload new photos or videos to the gallery ourselves and make basic changes to the information on line.

Our main clients are French but we have international guests coming who only understand english.

Ideally you would know how to link your creation to the existing domain name, how to make sure the email adresses remain the same and help us find the least expensive but best all in 1 proposition to make it as easy as possible to pay the yearly fee to the hosting platform / web name / etc :-)

Design wise we would like something creative, linked to films etc but without using to many clichés. The logo and a stamp have already been created and we would like to keep these (which has the colours we would like you to use).

It would be nice to maybe have a moving image when you first open the page, maybe the logo itself, something dynamic and visual...

Thank you for you time in reading this!

Margot & Ninon & Apolline
Team LRS

Target Market(s)

actors

Coding

Coded - Design and coding required

Number of Pages Required

5+ page

Font styles to use
Sans Serif

Colors
34a7d8

Requirements
Must have
• able to be read on all electronic devices
Nice to have
• some fun and humour / class
Should not have
• too corporate

```html
<!DOCTYPE html>
<html lang="fr">
<head>
<meta charset="utf-8">
<title>Lune Rouge Studio — Masterclasses pour comédiens</title>
<link rel="stylesheet" href="https://fonts.googleapis.com/css2?family=Open+Sans:ital,wght@0,400;0,600;0,700;0,800;1,400&display=swap">
<style>
  :root {
    --brand: #34a7d8;
    --brand-dark: #2a8fc2;
    --ink: #3a3a3a;
    --muted: #6f6f6f;
    --line: #e2e2e2;
    --soft: #f4f4f4;
    --slate: #6b6b6b;
    --night: #1d1a18;
    --white: #ffffff;
  }
  * { box-sizing: border-box; margin: 0; padding: 0; }
  html, body { width: 1200px; height: 3468px; overflow: hidden; }
  body { position: relative; background: var(--white); font-family: "Open Sans", Arial, sans-serif; color: var(--ink); }
  .abs { position: absolute; }
  .center { text-align: center; }

  /* header */
  .top-rule { left: 0; top: 0; width: 1200px; height: 5px; background: var(--brand); }
  .header-phone { left: 162px; top: 57px; font-size: 21px; font-weight: 600; color: var(--ink); display: flex; align-items: center; gap: 10px; }
  .brand { left: 420px; top: 44px; width: 360px; display: flex; justify-content: center; align-items: center; gap: 12px; }
  .brand-dot { width: 22px; height: 22px; border-radius: 50%; background: var(--brand); }
  .brand-name { font-size: 34px; font-weight: 400; color: var(--slate); letter-spacing: 1px; }
  .lang { left: 958px; top: 52px; width: 80px; height: 30px; border: 1px solid #cfcfcf; font-size: 11px; color: var(--muted); display: flex; align-items: center; justify-content: center; gap: 5px; background: var(--white); }
  .lang .flag { width: 14px; height: 9px; background: linear-gradient(#c8102e 0 33%, #fff 33% 66%, #012169 66%); }
  .nav { left: 0; top: 136px; width: 1200px; height: 60px; border-top: 1px solid var(--line); border-bottom: 1px solid var(--line); }
  .nav a { position: absolute; top: 20px; font-size: 14px; font-weight: 700; color: var(--ink); text-decoration: none; transform: translateX(-50%); letter-spacing: .3px; }

  /* hero */
  .hero { left: 0; top: 196px; width: 1200px; height: 549px; background: linear-gradient(120deg, #5d6e4e 0%, #8a8574 35%, #6f7a60 60%, #4a5840 100%); }
  .hero-shade { left: 0; top: 196px; width: 1200px; height: 549px; background: rgba(0,0,0,.18); }
  .hero-title { left: 0; top: 377px; width: 1200px; font-size: 38px; font-weight: 700; color: var(--white); }
  .hero-sub { left: 0; top: 437px; width: 1200px; font-size: 22px; font-weight: 700; color: var(--white); line-height: 33px; }
  .hero-arrow { top: 430px; width: 36px; height: 36px; border: 2px solid rgba(255,255,255,.7); border-radius: 50%; }

  /* service tiles */
  .tile { top: 677px; width: 291px; height: 220px; color: var(--white); text-align: center; }
  .tile-blue { background: var(--brand-dark); }
  .tile-grey { background: var(--slate); }
  .tile .icon { width: 84px; height: 84px; margin: 22px auto 0; border-radius: 50%; background: var(--white); display: flex; align-items: center; justify-content: center; }
  .tile h3 { margin-top: 22px; font-size: 17px; font-weight: 700; letter-spacing: .5px; }
  .tile p { margin: 12px 30px 0; font-size: 11px; line-height: 17px; }

  /* welcome */
  .section-title { left: 0; width: 1200px; font-size: 25px; font-weight: 800; color: var(--ink); letter-spacing: .5px; }
  .lead { left: 162px; width: 876px; font-size: 11.5px; line-height: 22px; color: var(--muted); text-align: center; }
  .btn-primary { left: 518px; top: 1128px; width: 164px; height: 36px; background: var(--brand-dark); color: var(--white); font-size: 12px; font-weight: 700; display: flex; align-items: center; justify-content: center; gap: 5px; }

  /* masterclasses */
  .band-soft { left: 0; width: 1200px; background: var(--soft); border-top: 1px solid var(--line); border-bottom: 1px solid var(--line); }
  .class-photo { top: 1364px; width: 271px; height: 185px; }
  .class-title { top: 1566px; font-size: 19px; font-weight: 700; color: var(--brand-dark); }
  .class-text { top: 1608px; width: 271px; font-size: 11px; line-height: 17px; color: var(--muted); }
  .btn-ghost { top: 1690px; width: 83px; height: 35px; border: 1px solid #9a9a9a; font-size: 9px; font-weight: 700; color: var(--ink); display: flex; align-items: center; justify-content: center; background: var(--white); }

  /* portfolio */
  .filters { left: 0; top: 1924px; width: 1200px; display: flex; justify-content: center; gap: 26px; font-size: 11px; font-weight: 600; color: var(--ink); }
  .filters .active { color: var(--brand-dark); }
  .folio { width: 282px; height: 231px; }
  .rule { left: 162px; top: 2510px; width: 876px; height: 2px; background: var(--line); }

  /* testimonials */
  .avatar { width: 130px; height: 130px; border-radius: 50%; border: 5px solid #e8e8e8; }
  .quote { width: 315px; font-size: 11.5px; line-height: 19px; color: var(--muted); font-style: italic; }
  .quote-name { font-size: 12px; font-weight: 700; color: var(--brand-dark); }
  .side-arrow { top: 2705px; }

  /* contact band */
  .contact { left: 0; top: 2858px; width: 1200px; height: 298px; background: linear-gradient(100deg, #2a221c 0%, #4a3a2c 45%, #2d2a20 100%); }
  .contact-shade { left: 0; top: 2858px; width: 1200px; height: 298px; background: rgba(10,8,6,.45); }
  .contact-line { left: 0; width: 1200px; color: var(--white); font-size: 27px; font-weight: 700; text-align: center; }

  /* footer */
  .footer { left: 0; top: 3156px; width: 1200px; height: 312px; background: var(--soft); }
  .stamp { left: 161px; top: 3204px; width: 154px; height: 154px; border-radius: 50%; background: #e9e3c9; border: 8px solid var(--brand-dark); }
  .foot-col { top: 3198px; }
  .foot-col h4 { font-size: 13px; font-weight: 700; color: var(--ink); margin-bottom: 12px; }
  .foot-col li { list-style: none; font-size: 11px; line-height: 22px; color: var(--muted); }
  .copyright { left: 162px; top: 3420px; font-size: 10.5px; color: var(--ink); }
  .social { top: 3412px; width: 34px; height: 34px; border-radius: 50%; }
</style>
</head>
<body>

<header>
  <div class="abs top-rule"></div>
  <div class="abs header-phone">
    <svg width="18" height="18" viewBox="0 0 24 24"><path fill="#2a8fc2" d="M6.6 10.8a15 15 0 006.6 6.6l2.2-2.2a1 1 0 011-.25 11.4 11.4 0 003.6.57 1 1 0 011 1V20a1 1 0 01-1 1A17 17 0 013 4a1 1 0 011-1h3.5a1 1 0 011 1c0 1.25.2 2.45.57 3.57a1 1 0 01-.25 1z"/></svg>
    +33 6 00 00 12 34
  </div>
  <div class="abs brand"><span class="brand-dot"></span><span class="brand-name">Lune Rouge Studio</span></div>
  <div class="abs lang"><span class="flag"></span>English ▾</div>
  <nav class="abs nav">
    <a style="left:206px">A PROPOS</a>
    <a style="left:317px">STAGES</a>
    <a style="left:421px">PHOTOS</a>
    <a style="left:525px">VIDEOS</a>
    <a style="left:631px">EVENEMENTS</a>
    <a style="left:768px">L'ÉQUIPE</a>
    <a style="left:895px">PARTENAIRES</a>
    <a style="left:1008px">BLOG</a>
  </nav>
</header>

<section class="hero-block">
  <div class="abs hero" role="img" aria-label="Photo d'un tournage en extérieur au bord d'une piscine, comédiens et caméra sous un parapluie"></div>
  <div class="abs hero-shade"></div>
  <h1 class="abs hero-title center">LUNE ROUGE STUDIO COMPANY</h1>
  <p class="abs hero-sub center">WE ARE AN ACTING SCHOOL THAT HOLDS MASTERCLASSES<br>FOR PROFESSIONAL ACTORS IN PARIS</p>
  <div class="abs hero-arrow" style="left:40px"><svg width="32" height="32" viewBox="0 0 32 32"><path d="M18 10l-6 6 6 6" stroke="#fff" stroke-width="2" fill="none"/></svg></div>
  <div class="abs hero-arrow" style="left:1118px"><svg width="32" height="32" viewBox="0 0 32 32"><path d="M14 10l6 6-6 6" stroke="#fff" stroke-width="2" fill="none"/></svg></div>
</section>

<section class="services">
  <div class="abs tile tile-blue" style="left:162px">
    <div class="icon"><svg width="44" height="44" viewBox="0 0 44 44"><rect x="6" y="16" width="22" height="16" rx="2" fill="#2a8fc2"/><path d="M28 21l10-5v16l-10-5z" fill="#2a8fc2"/><circle cx="12" cy="11" r="4" fill="#2a8fc2"/><circle cx="22" cy="11" r="4" fill="#2a8fc2"/></svg></div>
    <h3>CREATIVE</h3>
    <p>Des ateliers pensés pour explorer le jeu, oser et trouver sa voix devant la caméra.</p>
  </div>
  <div class="abs tile tile-grey" style="left:454px">
    <div class="icon"><svg width="44" height="44" viewBox="0 0 44 44"><rect x="8" y="18" width="28" height="18" fill="#555"/><path d="M8 11l27-5 1 6-27 5z" fill="#555"/></svg></div>
    <h3>CINEMA</h3>
    <p>Scènes tournées et montées comme sur un plateau, avec des réalisateurs en activité.</p>
  </div>
  <div class="abs tile tile-blue" style="left:745px">
    <div class="icon"><svg width="44" height="44" viewBox="0 0 44 44"><rect x="7" y="8" width="30" height="20" fill="none" stroke="#2a8fc2" stroke-width="3"/><path d="M22 28v6M16 38l6-4 6 4" stroke="#2a8fc2" stroke-width="3" fill="none"/></svg></div>
    <h3>TRAINING</h3>
    <p>Un suivi exigeant pour progresser, préparer un casting et enrichir sa bande démo.</p>
  </div>
</section>

<section class="welcome">
  <h2 class="abs section-title center" style="top:953px">WELCOME TO OUR COMPANY</h2>
  <p class="abs lead" style="top:1004px">Depuis plusieurs années, notre studio accueille des comédiennes et comédiens professionnels venus de France et d'ailleurs pour travailler le jeu face caméra. Chaque masterclass réunit un petit groupe autour d'un réalisateur, d'un directeur de casting ou d'un coach reconnu. On y tourne, on s'y regarde, on recommence, dans une ambiance bienveillante et exigeante à la fois. Les séances se déroulent en français ou en anglais selon les invités, dans des lieux choisis pour leur atmosphère de cinéma à Paris.</p>
  <div class="abs btn-primary">GET STARTED HERE <svg width="12" height="12" viewBox="0 0 12 12"><circle cx="6" cy="6" r="5.5" fill="#fff"/><path d="M5 3.5L7.5 6 5 8.5" stroke="#2a8fc2" stroke-width="1.5" fill="none"/></svg></div>
</section>

<section class="masterclasses">
  <div class="abs band-soft" style="top:1218px;height:567px"></div>
  <h2 class="abs section-title center" style="top:1256px">OUR MASTERCLASSES</h2>
  <p class="abs lead" style="top:1296px;left:262px;width:676px">Des stages courts et intenses, animés par des professionnels du cinéma et de la télévision, pour jouer, tourner et se revoir à l'image.</p>

  <div class="abs class-photo" style="left:162px;background:linear-gradient(135deg,#3c2e26,#7a5f48)" role="img" aria-label="Photo d'un groupe de comédiens en atelier dans une salle"></div>
  <div class="abs class-photo" style="left:462px;background:linear-gradient(135deg,#2a2620,#a88a52)" role="img" aria-label="Photo d'une séance de tournage sous des projecteurs"></div>
  <div class="abs class-photo" style="left:765px;background:linear-gradient(135deg,#2e2e2e,#9a9a9a)" role="img" aria-label="Photo en noir et blanc d'une répétition avec caméra"></div>

  <h3 class="abs class-title" style="left:162px">Jouer face caméra</h3>
  <h3 class="abs class-title" style="left:462px">Préparer un casting</h3>
  <h3 class="abs class-title" style="left:765px">Tourner une scène</h3>
  <p class="abs class-text" style="left:162px">Trois jours pour apprivoiser l'objectif, ajuster son jeu au cadre et se revoir avec un regard neuf.</p>
  <p class="abs class-text" style="left:462px">Travail des essais, choix des scènes et conseils concrets d'une directrice de casting.</p>
  <p class="abs class-text" style="left:765px">Une scène écrite, répétée puis tournée en conditions réelles avec une équipe image.</p>
  <div class="abs btn-ghost" style="left:162px">READ MORE</div>
  <div class="abs btn-ghost" style="left:462px">READ MORE</div>
  <div class="abs btn-ghost" style="left:765px">READ MORE</div>
</section>

<section class="portfolio">
  <h2 class="abs section-title center" style="top:1818px">PORTFOLIO</h2>
  <p class="abs lead" style="top:1864px;left:262px;width:676px">Quelques images de nos stages, de nos lieux de tournage et de nos soirées de rencontres entre comédiens et professionnels.</p>
  <div class="abs filters"><span class="active">ALL</span><span>COACHING</span><span>LIEU</span><span>SOIREES NETWORKING</span><span>STAGES</span></div>

  <div class="abs folio" style="left:162px;top:1972px;background:linear-gradient(135deg,#6a4a32,#c9a27a)" role="img" aria-label="Photo de deux comédiennes lisant un scénario à une table"></div>
  <div class="abs folio" style="left:460px;top:1972px;background:linear-gradient(135deg,#3f5a2c,#b13a36)" role="img" aria-label="Photo d'un tournage en jardin sous un parapluie rouge"></div>
  <div class="abs folio" style="left:758px;top:1972px;background:linear-gradient(135deg,#1e1e1e,#8a8a8a)" role="img" aria-label="Photo en noir et blanc d'un groupe de comédiens à une soirée"></div>
  <div class="abs folio" style="left:162px;top:2217px;background:linear-gradient(135deg,#4e5a2a,#b58a48)" role="img" aria-label="Photo de groupe des participants en extérieur"></div>
  <div class="abs folio" style="left:460px;top:2217px;background:linear-gradient(135deg,#2f4a28,#b8402e)" role="img" aria-label="Photo d'une comédienne et d'une opératrice caméra dans un jardin"></div>
  <div class="abs folio" style="left:758px;top:2217px;background:linear-gradient(180deg,#6b6450,#3c8aa0)" role="img" aria-label="Photo d'une maison de tournage avec piscine"></div>
  <div class="abs rule"></div>
</section>

<section class="testimonials">
  <h2 class="abs section-title center" style="top:2567px">NOS COMÉDIEN(NE)S PARLENT DE LUNE ROUGE STUDIO</h2>
  <svg class="abs side-arrow" style="left:70px" width="22" height="46" viewBox="0 0 22 46"><path d="M18 4L4 23l14 19" stroke="#c8c8c8" stroke-width="2" fill="none"/></svg>
  <svg class="abs side-arrow" style="left:1090px" width="22" height="46" viewBox="0 0 22 46"><path d="M4 4l14 19L4 42" stroke="#c8c8c8" stroke-width="2" fill="none"/></svg>

  <div class="abs avatar" style="left:157px;top:2663px;background:linear-gradient(135deg,#3a3a3a,#b0b0b0)" role="img" aria-label="Portrait de la comédienne Claire Vasseur"></div>
  <p class="abs quote" style="left:300px;top:2660px">« J'ai rencontré Ninon à l'occasion d'un tournage où je devais interpréter un personnage dans une situation extrême, elle m'a non seulement rassurée, fait travailler, mais elle m'a emmenée ailleurs… c'est une observatrice pointilleuse. »</p>
  <p class="abs quote-name" style="left:306px;top:2767px">CLAIRE VASSEUR</p>

  <div class="abs avatar" style="left:627px;top:2663px;background:linear-gradient(135deg,#4a6a3a,#c8402e)" role="img" aria-label="Portrait du comédien Julien Morand"></div>
  <p class="abs quote" style="left:770px;top:2660px">« J'ai rencontré Ninon à l'occasion d'un tournage où je devais interpréter un personnage dans une situation extrême, elle m'a non seulement rassuré, fait travailler, mais elle m'a emmené ailleurs… c'est une observatrice pointilleuse. »</p>
  <p class="abs quote-name" style="left:776px;top:2767px">JULIEN MORAND</p>
</section>

<section class="contact-band">
  <div class="abs contact" role="img" aria-label="Photo sombre d'un groupe de comédiens lors d'une soirée en extérieur"></div>
  <div class="abs contact-shade"></div>
  <p class="abs contact-line" style="top:2943px">Lune Rouge Studio</p>
  <p class="abs contact-line" style="top:2984px">contact@lune-rouge-studio.example</p>
  <p class="abs contact-line" style="top:3024px">+33 6 00 00 12 34</p>
</section>

<footer>
  <div class="abs footer"></div>
  <div class="abs stamp" role="img" aria-label="Tampon du studio"></div>
  <div class="abs foot-col" style="left:388px"><h4>LINKS</h4><ul><li>Nos masterclasses</li><li>Calendrier</li><li>Tarifs et inscriptions</li><li>Intervenants</li><li>Questions fréquentes</li></ul></div>
  <div class="abs foot-col" style="left:587px"><h4>HELP YOU</h4><ul><li>Your Account</li><li>Your Orders</li><li>Conditions de vente</li><li>Accès et horaires</li><li>Nous écrire</li></ul></div>
  <div class="abs foot-col" style="left:779px"><h4>WHAT WE DO</h4><ul><li>Jeu face caméra</li><li>Coaching privé</li><li>Préparation casting</li><li>Bandes démo</li><li>Soirées rencontres</li></ul></div>
  <div class="abs foot-col" style="left:964px"><h4>COMPANY</h4><ul><li>A propos</li><li>Stages</li><li>Photos</li><li>Videos</li><li>Evenements</li><li>L'équipe</li></ul></div>
  <p class="abs copyright">© 2016, All Copyrights are Reserved, Lune Rouge Studio, Terms of Use &nbsp;&nbsp; Privacy Policy &nbsp;&nbsp; Sitemap</p>
  <div class="abs social" style="left:899px;background:#55acee"></div>
  <div class="abs social" style="left:938px;background:#3b5998"></div>
  <div class="abs social" style="left:975px;background:#0e76a8"></div>
  <div class="abs social" style="left:1014px;background:#dd4b39"></div>
</footer>

</body>
</html>
```